Business Cards for company that supports physicians that do medical research

Need to create a business card for Qorvel Studies (www.qorvelstudies.example), a company devoted to supporting physicians who conduct medical research. The form of the card should match the message of research and information quest. I have provided the logo of the company as an uploaded file. Designs should be simple and slick aimed at very high end clients.

Target Market(s)

Medical doctors that are also researchers

Industry/Entity Type

Medical

Contact Information for Business Card

Should feature logo and fields for personal info:
Name/title
Phone /email

Font styles to use
Serif
Sans Serif

Requirements
Must have
• Qorvel logo and fields for personal info:
• Name: Bertrand Okonfu
• Title: VP Research and Senior Analyst
• Phone: 555-203-4719
• email: info@qorvelstudies.example
Nice to have
• Interesting cards that I've seen:
• 1- all black/charcoal or very dark background
• 2- Plastic - semi-transparent
• 3- non-standard height-width ratios
• 4- Functional cards -- USB drive incorporated
Should not have
• Too busy; needs to stay very simple

```html
<!DOCTYPE html>
<html lang="en">
<head>
<meta charset="utf-8">
<title>Qorvel Studies — Business Card</title>
<link href="https://fonts.googleapis.com/css2?family=Open+Sans:ital,wght@0,400;0,600;1,400&display=swap" rel="stylesheet">
<style>
  :root {
    --stage: #3c3c3c;
    --paper: #f7f7f7;
    --brand-blue: #1b78c2;
    --brand-green: #3cb54a;
    --ink-gray: #555555;
    --band-gray: #5e5e5e;
    --rule: #c9c9c9;
    --white: #ffffff;
  }
  * { box-sizing: border-box; margin: 0; padding: 0; }
  html, body {
    width: 1200px; height: 750px; overflow: hidden;
    background: var(--stage);
    font-family: "Open Sans", Arial, sans-serif;
  }
  .card {
    position: absolute; top: 228px;
    width: 461px; height: 263px; overflow: hidden;
  }
  .card--front { left: 124px; background: var(--paper); }
  .card--back { left: 618px; background: var(--brand-blue); }

  .wordmark {
    position: absolute; left: 0; right: 0;
    display: flex; align-items: center; justify-content: center; gap: 10px;
    font-weight: 600; letter-spacing: 0.5px; white-space: nowrap;
  }
  .card--front .wordmark { top: 62px; font-size: 36px; color: var(--brand-blue); }
  .card--back .wordmark { top: 84px; font-size: 38px; color: var(--white); }
  .wordmark__dot { width: 14px; height: 14px; border-radius: 50%; background: var(--brand-green); flex: none; }
  .card--back .wordmark__dot { background: var(--white); }

  .person {
    position: absolute; right: 236px; top: 166px; text-align: right; white-space: nowrap;
  }
  .person__name { font-size: 16px; font-weight: 600; color: var(--brand-blue); line-height: 22px; }
  .person__title { font-size: 12px; color: var(--brand-green); line-height: 18px; }

  .divider {
    position: absolute; left: 239px; top: 160px; width: 1px; height: 56px; background: var(--rule);
  }

  .contact {
    position: absolute; left: 257px; top: 162px; list-style: none;
  }
  .contact__item {
    display: flex; align-items: center; gap: 5px;
    font-size: 11px; color: var(--ink-gray); height: 18px;
  }
  .contact__icon { width: 12px; height: 12px; flex: none; }

  .bands { position: absolute; left: 0; bottom: 0; width: 100%; height: 8px; }
  .band { position: absolute; top: 0; height: 8px; }
  .band--blue { left: 0; width: 150px; background: var(--brand-blue); }
  .band--green { left: 152px; width: 154px; background: var(--brand-green); }
  .band--gray { left: 308px; width: 153px; background: var(--band-gray); }

  .backdrop {
    position: absolute; inset: 0;
    background: linear-gradient(180deg, #1f83cc 0%, #1a77c0 100%);
  }
  .web {
    position: absolute; left: 0; right: 0; top: 208px; text-align: center;
    font-size: 11px; font-style: italic; letter-spacing: 2px; color: var(--white);
  }
</style>
</head>
<body>

  <section class="card card--front">
    <div class="wordmark"><span class="wordmark__dot"></span>Qorvel Studies</div>

    <div class="person">
      <p class="person__name">Bertrand Okonfu</p>
      <p class="person__title">VP Research &amp; Senior Analyst</p>
    </div>

    <div class="divider"></div>

    <ul class="contact">
      <li class="contact__item">
        <svg class="contact__icon" viewBox="0 0 24 24"><path fill="#1b78c2" d="M6.6 10.8a15.1 15.1 0 0 0 6.6 6.6l2.2-2.2a1 1 0 0 1 1-.25 11.4 11.4 0 0 0 3.6.57 1 1 0 0 1 1 1V20a1 1 0 0 1-1 1A17 17 0 0 1 3 4a1 1 0 0 1 1-1h3.5a1 1 0 0 1 1 1c0 1.25.2 2.45.57 3.6a1 1 0 0 1-.25 1z"/></svg>
        555-203-4719
      </li>
      <li class="contact__item">
        <svg class="contact__icon" viewBox="0 0 24 24"><rect x="2" y="5" width="20" height="14" fill="#1b78c2"/><path d="M2 5l10 8 10-8" fill="none" stroke="#fff" stroke-width="1.8"/></svg>
        info@qorvelstudies.example
      </li>
      <li class="contact__item">
        <svg class="contact__icon" viewBox="0 0 24 24"><circle cx="12" cy="12" r="10" fill="#1b78c2"/><ellipse cx="12" cy="12" rx="4" ry="10" fill="none" stroke="#fff" stroke-width="1.5"/><path d="M2 12h20" stroke="#fff" stroke-width="1.5"/></svg>
        www.qorvelstudies.example
      </li>
    </ul>

    <div class="bands">
      <span class="band band--blue"></span>
      <span class="band band--green"></span>
      <span class="band band--gray"></span>
    </div>
  </section>

  <section class="card card--back">
    <div class="backdrop" role="img" aria-label="Tone-on-tone blue repeating brand pattern"></div>
    <div class="wordmark"><span class="wordmark__dot"></span>Qorvel Studies</div>
    <p class="web">www.qorvelstudies.example</p>
  </section>

</body>
</html>
```